Dynamic Business Card for Sports Supplements Company

Hi! I'm looking for an awesome business card to match my existing sports supplement company. I have uploaded my current company logo and screenshot of the front page of my website.

I would like to have something dynamic and interesting and utilize the colors in the website - the reds and purples

The business card should be double sided and focus on a unique eye-catching design on the back and include all the relevant company info.

Most importantly, it should say somewhere: "Sign up on our website for a coupon code."

Target Market(s)

Mostly for women gym goers but it shouldn't be too feminine. It should be in keeping with the website design. It should flow and clearly be connected to it

Industry/Entity Type

Business

Contact Information for Business Card

Lorraine K. Vestal
CEO
LVestal@Quorvanexco.com
www.quorvanexco.com
555.417.3820
P.O. Box 47315
Fenwick, Vermont 00000

Sign up on our website for a coupon code

Font styles to use
Serif
Sans Serif
Other font styles liked:
• Novecento font family and "Quorvanex" is in AR Destine font

Requirements
Must have
• One side should be a bold Quorvanex logo design. Even just the symbol itself may be o.k. (see attached file)

```html
<!DOCTYPE html>
<html lang="en">
<head>
<meta charset="utf-8">
<title>Quorvanex Business Card</title>
<link rel="stylesheet" href="https://fonts.googleapis.com/css2?family=Open+Sans:ital,wght@0,400;0,600;0,800;1,400&display=swap">
<style>
  :root {
    --backdrop: #7a5236;
    --card-black: #000000;
    --brand-red: #e31e2b;
    --pattern-red: #e8202e;
    --white: #ffffff;
    --muted-grey: #bdbdbd;
    --divider: #4a4a4a;
  }
  * { margin: 0; padding: 0; box-sizing: border-box; }
  html, body {
    width: 1200px;
    height: 987px;
    overflow: hidden;
    background: var(--backdrop);
    font-family: "Open Sans", Arial, sans-serif;
  }
  .canvas { position: relative; width: 1200px; height: 987px; }

  .card {
    position: absolute;
    width: 616px;
    height: 352px;
    overflow: hidden;
    box-shadow: 0 4px 10px rgba(0,0,0,0.35);
  }

  /* Front side */
  .card-front { left: 293px; top: 130px; background: var(--card-black); }
  .brand-block {
    position: absolute;
    left: 0;
    width: 352px;
    top: 92px;
    text-align: center;
  }
  .brand-mark {
    display: block;
    width: 64px;
    height: 64px;
    margin: 0 auto 38px;
    background: var(--brand-red);
  }
  .brand-name {
    color: var(--white);
    font-weight: 800;
    font-size: 32px;
    line-height: 1;
    letter-spacing: 1.5px;
    text-transform: uppercase;
  }
  .brand-tagline {
    margin-top: 4px;
    color: var(--muted-grey);
    font-size: 9.5px;
    letter-spacing: 3px;
    text-transform: uppercase;
  }
  .divider {
    position: absolute;
    left: 315px;
    top: 73px;
    width: 1px;
    height: 172px;
    background: var(--divider);
  }
  .contact {
    position: absolute;
    left: 341px;
    top: 82px;
    color: var(--white);
    font-size: 15px;
    line-height: 22px;
  }
  .contact-name {
    color: var(--brand-red);
    font-size: 20px;
    font-weight: 600;
    text-transform: uppercase;
    line-height: 24px;
  }
  .contact-role { margin-bottom: 12px; }
  .contact-address { margin-bottom: 8px; }
  .contact-label { color: var(--brand-red); font-weight: 600; }

  .web-band {
    position: absolute;
    left: 0;
    top: 310px;
    width: 463px;
    height: 27px;
    background: var(--brand-red);
    color: var(--white);
    font-size: 15px;
    letter-spacing: 2.5px;
    line-height: 27px;
    text-align: center;
  }
  .white-band {
    position: absolute;
    left: 497px;
    right: 0;
    top: 310px;
    height: 27px;
    background: var(--white);
  }

  /* Back side */
  .card-back { left: 292px; top: 506px; background: var(--brand-red); }
  .back-pattern {
    position: absolute;
    inset: 0;
    background: linear-gradient(180deg, var(--pattern-red), var(--brand-red));
  }
  .back-brand {
    position: absolute;
    left: 144px;
    top: 136px;
    color: var(--white);
  }
  .back-brand .brand-name { font-size: 42px; letter-spacing: 1.8px; }
  .back-brand .brand-tagline { font-size: 11.5px; letter-spacing: 3.3px; margin-top: 3px; color: var(--white); }
  .coupon-note {
    margin-top: 2px;
    font-style: italic;
    font-size: 17px;
  }
</style>
</head>
<body>
<main class="canvas">
  <section class="card card-front" aria-label="Business card front">
    <div class="brand-block">
      <span class="brand-mark" aria-hidden="true"></span>
      <div class="brand-name">Quorvanex</div>
      <div class="brand-tagline">Your Performance Partner</div>
    </div>
    <div class="divider"></div>
    <div class="contact">
      <div class="contact-name">Lorraine K. Vestal</div>
      <div class="contact-role">CEO</div>
      <div class="contact-address">P.O. Box 47315<br>Fenwick, Vermont 00000</div>
      <div><span class="contact-label">Phone:</span> 555.417.3820</div>
      <div>LVestal@Quorvanexco.com</div>
    </div>
    <div class="web-band">www.quorvanexco.com</div>
    <div class="white-band"></div>
  </section>

  <section class="card card-back" aria-label="Business card back">
    <div class="back-pattern" role="img" aria-label="Repeating red chevron brand pattern"></div>
    <div class="back-brand">
      <div class="brand-name">Quorvanex</div>
      <div class="brand-tagline">Your Performance Partner</div>
      <div class="coupon-note">Sign up on our website for a coupon code</div>
    </div>
  </section>
</main>
</body>
</html>
```